AnswerCraft Website Redesign

I'm looking to redesign our website AnswerCraft.com. The main goal is to give it a fresh design that is easy on the eyes and pushes the users to creating an account.

Our platform is very simple and we only do one thing, we use ai to generate response to customer and product reviews.

See attached file to see the pricing section style.

On the homepage just under the hero section, I would like to include the wording:
"Write replies to the reviews you get on sites like:" then show the logos like we have on our register page: https://app.answercraft.com/public/index.php

Target Market(s)

Business owners with brick and morter business or any business or product that gets online reviews

Industry/Entity Type

reputation management

Number of Pages Required

2 page

Requirements
Must have
• Home page and pricing page

```html
<!DOCTYPE html>
<html lang="en">
<head>
<meta charset="utf-8">
<title>AnswerCraft – Write personalized responses to reviews</title>
<link rel="stylesheet" href="https://fonts.googleapis.com/css2?family=Roboto:wght@400;500;700&family=Lato:wght@400;700&display=swap">
<style>
:root{
  --navy:#1f2f8f;
  --navy-deep:#172477;
  --orange:#f7941d;
  --ink:#1d1d1d;
  --muted:#5b5b5b;
  --line:#c9c9c9;
  --ring:#c9d0ee;
  --white:#ffffff;
  --footer:#0d0d0d;
}
*{box-sizing:border-box;margin:0;padding:0}
html,body{width:1200px;height:4428px;overflow:hidden}
body{position:relative;background:var(--white);font-family:'Lato',sans-serif;color:var(--ink)}
.abs{position:absolute}
.accent{color:var(--orange)}
.btn{position:absolute;display:flex;align-items:center;justify-content:center;font-family:'Roboto',sans-serif;font-weight:700;font-size:14px;color:var(--white);background:var(--orange);border-radius:6px;text-transform:uppercase;letter-spacing:.2px}
.btn-outline{background:transparent;border:2px solid var(--orange)}

/* header */
.site-header{position:absolute;left:0;top:0;width:1200px;height:113px;background:var(--white)}
.brand{position:absolute;display:flex;align-items:center;gap:12px;font-family:'Roboto',sans-serif;font-weight:700;color:var(--navy)}
.brand-mark{width:30px;height:30px;border:4px solid var(--navy);border-radius:6px}
.nav{position:absolute;top:47px;font-family:'Roboto',sans-serif;font-size:14px;color:#333}

/* hero */
.hero{position:absolute;left:0;top:113px;width:1200px;height:557px;border-radius:0 0 170px 170px;overflow:hidden;background:linear-gradient(110deg,#8f9ac4 0%,#5a6aa8 35%,#2c3a7a 60%,#7684bc 100%)}
.hero-title{position:absolute;left:389px;top:150px;width:420px;text-align:center;font-family:'Roboto',sans-serif;font-weight:700;font-size:33px;line-height:51px;color:var(--white)}
.dot{position:absolute;width:10px;height:10px;border-radius:50%;background:var(--white)}

/* platforms */
.section-title{position:absolute;left:0;width:1200px;text-align:center;font-family:'Roboto',sans-serif;font-weight:700;color:var(--ink)}
.platform{position:absolute;top:837px;width:158px;height:158px;border-radius:50%;background:var(--ring);display:flex;align-items:center;justify-content:center}
.platform span{width:134px;height:134px;border-radius:50%;background:var(--navy);display:flex;align-items:center;justify-content:center;color:var(--white);font-family:'Lato',sans-serif;font-weight:700;font-size:22px}
.pager{position:absolute;width:11px;height:11px;border-radius:50%;background:#bdbdbd}

/* how it works */
.how{position:absolute;left:0;top:1133px;width:1200px;height:583px;background:linear-gradient(100deg,#eceef3 0%,#e2e5ee 55%,#c9cfe0 100%)}
.how-lead{position:absolute;left:110px;top:180px;font-family:'Roboto',sans-serif;font-size:19px;color:var(--navy)}
.how-text{position:absolute;left:110px;top:230px;width:420px;font-size:15px;line-height:25px;color:var(--muted)}
.how-point{position:absolute;left:156px;font-family:'Roboto',sans-serif;font-size:19px;color:var(--ink)}
.how-bullet{position:absolute;left:124px;width:10px;height:10px;border-radius:50%;background:var(--orange)}
.how-rule{position:absolute;left:112px;width:413px;height:1px;background:#8a8a8a}
.how-visual{position:absolute;left:598px;top:197px;width:492px;height:292px;border-radius:6px;background:linear-gradient(120deg,#ffffff 0%,#eef0ff 50%,#fbe3ee 100%);box-shadow:0 4px 14px rgba(0,0,0,.12)}

/* pricing */
.plan{position:absolute;top:1963px;width:463px;height:547px;background:var(--white);border-radius:20px;box-shadow:0 4px 18px rgba(0,0,0,.14);text-align:center}
.plan h3{position:absolute;left:0;top:36px;width:100%;font-family:'Roboto',sans-serif;font-weight:500;font-size:25px;color:var(--ink)}
.plan .sub{position:absolute;left:0;top:78px;width:100%;font-size:14px;color:#444}
.plan .rule{position:absolute;left:48px;top:120px;width:367px;height:1px;background:#ddd}
.plan .price{position:absolute;left:0;top:138px;width:100%;font-family:'Roboto',sans-serif;font-weight:700;font-size:20px}
.range{position:absolute;top:176px;font-family:'Roboto',sans-serif;font-weight:700;font-size:14px}
.slider{position:absolute;left:72px;top:202px;width:320px;height:7px;border-radius:4px;background:#e0e0e0}
.slider i{display:block;width:140px;height:7px;border-radius:4px;background:var(--navy)}
.credits{position:absolute;left:0;top:222px;width:100%;font-family:'Roboto',sans-serif;font-size:15px}
.features{position:absolute;top:355px;list-style:none;text-align:left;font-size:15px;color:#333}
.features li{display:flex;align-items:center;gap:14px;height:34px}
.tick{width:13px;height:13px;border-radius:50%;background:var(--navy);display:flex;align-items:center;justify-content:center}

/* faq */
.faq{position:absolute;left:0;top:2596px;width:1200px;height:704px;background:linear-gradient(160deg,#c3cbe6 0%,#aeb9dc 50%,#c0c8e4 100%)}
.faq-item{position:absolute;left:167px;width:867px;background:var(--white);box-shadow:0 2px 8px rgba(0,0,0,.15)}
.faq-q{position:absolute;left:30px;top:28px;font-family:'Roboto',sans-serif;font-size:17px;color:#333}
.faq-a{position:absolute;left:30px;top:68px;width:700px;font-size:12px;line-height:22px;color:#666}
.faq-toggle{position:absolute;right:28px;top:22px;font-family:'Roboto',sans-serif;font-weight:700;font-size:22px;color:#333}

/* benefits */
.benefit{position:absolute;top:3510px;width:300px;height:455px;background:var(--white);box-shadow:0 3px 12px rgba(0,0,0,.13);text-align:center}
.benefit-visual{position:absolute;left:30px;top:10px;width:240px;height:220px;border-radius:10px;background:linear-gradient(135deg,#e8ebfa 0%,#c9d1f2 60%,#fde6c7 100%)}
.benefit h4{position:absolute;left:0;top:250px;width:100%;font-family:'Roboto',sans-serif;font-weight:500;font-size:18px}
.benefit p{position:absolute;left:20px;top:288px;width:260px;font-size:14px;line-height:25px;color:#444}
.arrow{position:absolute;top:3779px;width:44px;height:44px;border-radius:50%;display:flex;align-items:center;justify-content:center}

/* footer */
.site-footer{position:absolute;left:0;top:4055px;width:1200px;height:373px;background:var(--footer);color:var(--white)}
.foot-col h5{font-family:'Roboto',sans-serif;font-weight:700;font-size:19px;margin-bottom:14px}
.foot-col{position:absolute;top:68px}
.foot-col li{list-style:none;font-size:14px;line-height:26px;color:#ddd}
.foot-col li::before{content:"»";margin-right:12px}
.social{position:absolute;top:4247px;width:36px;height:36px;border-radius:50%;background:var(--orange)}
.contact-row{display:flex;gap:12px;font-size:14px;line-height:25px;color:#ddd;margin-bottom:14px}
</style>
</head>
<body>

<header class="site-header">
  <div class="brand" style="left:110px;top:36px;font-size:30px"><span class="brand-mark"></span>AnswerCraft</div>
  <span class="nav" style="left:415px">WHY REPLY?</span>
  <span class="nav" style="left:548px">HOW IT WORKS</span>
  <span class="nav" style="left:704px">PRICING</span>
  <span class="nav" style="left:808px">BLOG</span>
  <span class="nav" style="left:893px">LOGIN</span>
  <a class="btn" style="left:983px;top:33px;width:105px;height:47px">Try Free</a>
</header>

<section class="hero" role="img" aria-label="Photo of a hand pointing at floating review cards with star ratings">
  <svg class="abs" style="left:0;top:0" width="1200" height="557" viewBox="0 113 1200 557">
    <path d="M373 190 H826 Q866 190 866 230 V470 Q866 510 826 510 H760 L753 640 L636 510 H373 Q333 510 333 470 V230 Q333 190 373 190 Z" fill="#ffffff"/>
    <rect x="367" y="223" width="463" height="254" rx="20" fill="#1f2f8f"/>
  </svg>
  <h1 class="hero-title">WRITE PERSONALIZED RESPONSES TO REVIEWS IN 10 SECONDS!</h1>
  <a class="btn" style="left:455px;top:327px;width:148px;height:45px">Start for free</a>
  <a class="btn btn-outline" style="left:617px;top:327px;width:127px;height:45px">Learn more</a>
  <span class="dot" style="left:568px;top:504px"></span>
  <span class="dot" style="left:584px;top:504px"></span>
  <span class="dot" style="left:600px;top:504px"></span>
  <span class="dot" style="left:616px;top:504px"></span>
</section>

<h2 class="section-title" style="top:750px;font-size:29px;font-weight:500">Write replies to the reviews you <span class="accent">get on sites like</span></h2>
<div class="platform" style="left:120px"><span>Quelvo</span></div>
<div class="platform" style="left:324px"><span>Nestaro</span></div>
<div class="platform" style="left:528px"><span>Ratevane</span></div>
<div class="platform" style="left:728px"><span>Cartwell</span></div>
<div class="platform" style="left:931px"><span>Yumpa</span></div>
<span class="pager" style="left:562px;top:1038px"></span>
<span class="pager" style="left:579px;top:1038px;background:var(--orange)"></span>
<span class="pager" style="left:596px;top:1038px"></span>
<span class="pager" style="left:613px;top:1038px"></span>

<section class="how">
  <h2 class="section-title" style="top:86px;font-size:28px;font-weight:500">How it <span class="accent">works</span></h2>
  <p class="how-lead">1 minute account creation</p>
  <p class="how-text">Gain access to the most powerful tool for writing unique and personal responses to the reviews your customers leave your business.</p>
  <span class="how-bullet" style="top:352px"></span>
  <p class="how-point" style="top:345px">We make it way too simple!</p>
  <span class="how-rule" style="top:399px"></span>
  <span class="how-bullet" style="top:438px"></span>
  <p class="how-point" style="top:431px">Only a 10 second wait</p>
  <span class="how-rule" style="top:485px"></span>
  <div class="how-visual" role="img" aria-label="Illustration of a review reply screen with star ratings, reaction emojis and a submit button"></div>
</section>

<h2 class="section-title" style="top:1800px;font-size:24px;font-weight:500;line-height:42px">Never worry about having to come up with a unique <span class="accent">response</span><br>to each <span class="accent">review</span> ever again!</h2>
<p class="abs" style="left:0;top:1898px;width:1200px;text-align:center;font-size:15px;color:#333">If your business, product or service receives reviews, this tool will save you hundreds of hours.</p>

<article class="plan" style="left:110px">
  <h3>Monthly Subscriptions</h3>
  <p class="sub">Perfect for getting started for one business/product</p>
  <span class="rule"></span>
  <p class="price">Starts at $9.99 / month</p>
  <span class="range" style="left:72px">50k</span>
  <span class="range" style="right:70px">700k</span>
  <div class="slider"><i></i></div>
  <p class="credits">5000 word credits</p>
  <a class="btn" style="left:162px;top:280px;width:140px;height:42px">Start for free</a>
  <ul class="features" style="left:112px">
    <li><span class="tick"><svg width="8" height="8" viewBox="0 0 8 8"><path d="M1 4 L3 6 L7 2" stroke="#fff" stroke-width="1.5" fill="none"/></svg></span>Personalized responses</li>
    <li><span class="tick"><svg width="8" height="8" viewBox="0 0 8 8"><path d="M1 4 L3 6 L7 2" stroke="#fff" stroke-width="1.5" fill="none"/></svg></span>30+ Languages</li>
    <li><span class="tick"><svg width="8" height="8" viewBox="0 0 8 8"><path d="M1 4 L3 6 L7 2" stroke="#fff" stroke-width="1.5" fill="none"/></svg></span>Auto-Save</li>
    <li><span class="tick"><svg width="8" height="8" viewBox="0 0 8 8"><path d="M1 4 L3 6 L7 2" stroke="#fff" stroke-width="1.5" fill="none"/></svg></span>Revision History</li>
    <li><span class="tick"><svg width="8" height="8" viewBox="0 0 8 8"><path d="M1 4 L3 6 L7 2" stroke="#fff" stroke-width="1.5" fill="none"/></svg></span>Assign members usage limits</li>
  </ul>
</article>

<article class="plan" style="left:626px">
  <h3>Agency Subscriptions</h3>
  <p class="sub">Perfect for multiple clients/products per month</p>
  <span class="rule"></span>
  <p class="price">Starting at $75.00 / month</p>
  <a class="btn" style="left:162px;top:280px;width:140px;height:42px">Start for free</a>
  <ul class="features" style="left:112px">
    <li><span class="tick"><svg width="8" height="8" viewBox="0 0 8 8"><path d="M1 4 L3 6 L7 2" stroke="#fff" stroke-width="1.5" fill="none"/></svg></span>Everything in the Startup plan</li>
    <li><span class="tick"><svg width="8" height="8" viewBox="0 0 8 8"><path d="M1 4 L3 6 L7 2" stroke="#fff" stroke-width="1.5" fill="none"/></svg></span>Dedicated Account Manager</li>
    <li><span class="tick"><svg width="8" height="8" viewBox="0 0 8 8"><path d="M1 4 L3 6 L7 2" stroke="#fff" stroke-width="1.5" fill="none"/></svg></span>Onboarding &amp; Training</li>
    <li><span class="tick"><svg width="8" height="8" viewBox="0 0 8 8"><path d="M1 4 L3 6 L7 2" stroke="#fff" stroke-width="1.5" fill="none"/></svg></span>Unlimited Integrations</li>
  </ul>
</article>

<section class="faq" role="region" aria-label="Frequently asked questions">
  <h2 class="section-title" style="top:80px;font-size:28px;font-weight:500">Frequently asked <span class="accent">questions</span></h2>
  <div class="faq-item" style="top:164px;height:148px">
    <p class="faq-q">Why is it important to respond to Quelvo reviews?</p>
    <span class="faq-toggle">−</span>
    <p class="faq-a">Responding to Quelvo reviews is vital for your business's success in local search results. By responding to both negative and positive feedback, you show customers that you're committed to listening to their concerns and exceeding their expectations.</p>
  </div>
  <div class="faq-item" style="top:339px;height:80px"><p class="faq-q">Why is it important to respond to negative reviews?</p><span class="faq-toggle">+</span></div>
  <div class="faq-item" style="top:442px;height:80px"><p class="faq-q">How can I trust someone who doesn't work at my business to reply to reviews on my behalf?</p><span class="faq-toggle">+</span></div>
  <div class="faq-item" style="top:545px;height:80px"><p class="faq-q">Which online review sites does AnswerCraft.com support?</p><span class="faq-toggle">+</span></div>
</section>

<h2 class="section-title" style="top:3375px;font-size:25px;font-weight:500;line-height:42px">It's simple. Our tool writes replies and responses to the <span class="accent">reviews</span><br>your <span class="accent">customers leave</span>. Doesn't matter if it's 1 or 5 stars.</h2>

<div class="arrow" style="left:48px;border:2px solid var(--navy)"><svg width="14" height="14" viewBox="0 0 14 14"><path d="M9 2 L4 7 L9 12" stroke="#1f2f8f" stroke-width="2" fill="none"/></svg></div>
<div class="arrow" style="left:1113px;background:var(--navy)"><svg width="14" height="14" viewBox="0 0 14 14"><path d="M5 2 L10 7 L5 12" stroke="#fff" stroke-width="2" fill="none"/></svg></div>

<article class="benefit" style="left:112px">
  <div class="benefit-visual" role="img" aria-label="Illustration of a review card with a written business reply"></div>
  <h4>Improved SEO</h4>
  <p>Quelvo loves seeing you leave a reply to your reviews and will give you a boost in their search results and local SEO.</p>
  <a class="btn" style="left:93px;top:380px;width:114px;height:40px">Learn more</a>
</article>
<article class="benefit" style="left:450px">
  <div class="benefit-visual" role="img" aria-label="Illustration of a customer review with a thoughtful reply"></div>
  <h4>Build Customer Trust</h4>
  <p>Customers want to know there are humans behind your companies product or service. Show them you value their</p>
  <a class="btn" style="left:93px;top:380px;width:114px;height:40px">Learn more</a>
</article>
<article class="benefit" style="left:788px">
  <div class="benefit-visual" role="img" aria-label="Illustration of a positive rental review and its reply"></div>
  <h4>Convert New Customers</h4>
  <p>FACT: Potential customers read reviews before making a decision. Give a good first impression with personalized</p>
  <a class="btn" style="left:93px;top:380px;width:114px;height:40px">Learn more</a>
</article>

<footer class="site-footer">
  <div class="brand" style="left:110px;top:100px;font-size:32px;color:#fff"><span class="brand-mark" style="border-color:#fff"></span>AnswerCraft</div>
  <div class="foot-col" style="left:432px"><h5>Quick Links</h5><ul><li>Why Reply?</li><li>How It Works</li><li>Pricing</li><li>Blog</li></ul></div>
  <div class="foot-col" style="left:638px"><h5>Our Company</h5><ul><li>Blog</li><li>Privacy Policy</li><li>Contact</li><li>Sitemap</li></ul></div>
  <div class="foot-col" style="left:863px;width:250px">
    <h5>Contact us</h5>
    <div class="contact-row"><svg width="12" height="16" viewBox="0 0 12 16"><path d="M6 0 C2.7 0 0 2.6 0 5.8 C0 10 6 16 6 16 C6 16 12 10 12 5.8 C12 2.6 9.3 0 6 0 Z" fill="#fff"/><circle cx="6" cy="6" r="2.2" fill="#0d0d0d"/></svg><span>Lorem ipsum dolor sit<br>amet, consectetur adipiscing</span></div>
    <div class="contact-row"><svg width="14" height="14" viewBox="0 0 14 14"><path d="M3 1 L5 1 L6 4 L4.5 5.5 C5.5 7.5 6.5 8.5 8.5 9.5 L10 8 L13 9 L13 11 C13 12 12 13 11 13 C5.5 13 1 8.5 1 3 C1 2 2 1 3 1 Z" fill="#fff"/></svg><span>+1 (555) 010 0199</span></div>
    <div class="contact-row"><svg width="15" height="12" viewBox="0 0 15 12"><rect x="0.5" y="0.5" width="14" height="11" fill="#fff"/><path d="M1 1 L7.5 7 L14 1" stroke="#0d0d0d" fill="none"/></svg><span>info@answercraft.com</span></div>
  </div>
  <span class="abs" style="left:390px;top:80px;width:1px;height:200px;background:#222"></span>
  <span class="abs" style="left:0;top:290px;width:1200px;height:1px;background:#222"></span>
  <p class="abs" style="left:0;top:310px;width:1200px;text-align:center;font-size:14px;color:#ddd">©Copyrights 2023 AnswerCraft &nbsp;|&nbsp; All Rights Reserved</p>
</footer>
<span class="social" style="left:110px" role="img" aria-label="Social profile link"></span>
<span class="social" style="left:154px" role="img" aria-label="Social profile link"></span>
<span class="social" style="left:197px" role="img" aria-label="Social profile link"></span>
<span class="social" style="left:240px" role="img" aria-label="Social profile link"></span>

</body>
</html>
```